Clear Plastic Card Design

I am looking to have a business card designed from my logo icon. I am looking to match the style of a different business card I have attached in the files.
Looking for a card that is plastic, with layers of transparency in the shape of my logo icon (also attached in the files) - not a circle like the other card. The winning design will incorporate the red icon logo on the front and back and include the charity's name, "Light for the Weary Souls" in the same or similar font, as well as an email and phone number. For now, use the email: email@lightfortheweary-mail.org and the phone number 555-382-7194.
We like how the sample business card has transparency, partial and full opacity layers and a matching color scheme. Files will need to be in vector so that our business card printing company can work with it.
UPDATE:
We've some excellent designs in, thank you everyone! I got an early review from the owner, and he requested a minor redirect to find his perfect design. He wants the design to stand out by NOT being a rectangle. Try instead a circle, square, or best yet - something that falls in the outline of the logo icon, either fully or partially. Thank you, everyone!
Light for the Weary Souls text should be incorporated as well as a phone and email.

```html
<!DOCTYPE html>
<html lang="en">
<head>
<meta charset="utf-8">
<title>Light for the Weary Souls – Clear Business Card</title>
<link rel="stylesheet" href="https://fonts.googleapis.com/css2?family=Questrial&family=Open+Sans:wght@400&display=swap">
<style>
  :root {
    --backdrop-top: #e2d8ca;
    --backdrop-bottom: #cdbfab;
    --clear-layer: rgba(255, 255, 255, 0.38);
    --frost-layer: rgba(255, 255, 255, 0.55);
    --card-edge: rgba(255, 255, 255, 0.85);
    --ink: #111111;
    --accent: #d3420f;
    --brand-red: #c41f1c;
    --rule: #2a2a2a;
  }
  * { margin: 0; padding: 0; box-sizing: border-box; }
  html, body {
    width: 1200px;
    height: 926px;
    overflow: hidden;
  }
  body {
    background: linear-gradient(180deg, var(--backdrop-top) 0%, var(--backdrop-bottom) 100%);
  }
  .canvas {
    position: relative;
    width: 1200px;
    height: 926px;
  }
  .card-shadow {
    position: absolute;
    left: 150px;
    top: 215px;
    width: 895px;
    height: 499px;
    filter: drop-shadow(0 8px 16px rgba(0, 0, 0, 0.14));
  }
  .card {
    position: relative;
    width: 100%;
    height: 100%;
    clip-path: polygon(70px 0, 100% 0, 100% calc(100% - 70px), calc(100% - 70px) 100%, 0 100%, 0 70px);
    background: var(--clear-layer);
    backdrop-filter: blur(2px);
  }
  .card__outline {
    position: absolute;
    inset: 0;
    width: 100%;
    height: 100%;
    pointer-events: none;
  }
  .card__frost {
    position: absolute;
    left: 0;
    top: 0;
    width: 372px;
    height: 100%;
    background: var(--frost-layer);
  }
  .card__band {
    position: absolute;
    left: 372px;
    top: 0;
    width: 28px;
    height: 100%;
    background: rgba(255, 255, 255, 0.12);
  }
  .brand-mark {
    position: absolute;
    left: 80px;
    top: 123px;
    width: 258px;
    height: 253px;
    display: flex;
    flex-direction: column;
    justify-content: center;
    gap: 18px;
  }
  .brand-mark__square {
    width: 110px;
    height: 110px;
    background: var(--brand-red);
  }
  .brand-mark__name {
    font-family: "Questrial", sans-serif;
    font-size: 30px;
    line-height: 1.15;
    color: var(--brand-red);
  }
  .details {
    position: absolute;
    left: 368px;
    top: 118px;
    width: 445px;
  }
  .details__name {
    font-family: "Questrial", sans-serif;
    font-weight: 400;
    font-size: 66px;
    line-height: 68px;
    color: var(--ink);
    letter-spacing: -0.5px;
  }
  .details__rule {
    height: 2px;
    background: var(--rule);
    width: 438px;
  }
  .details__rule--top { margin-top: 8px; }
  .details__phone {
    font-family: "Open Sans", sans-serif;
    font-size: 58px;
    line-height: 76px;
    color: var(--accent);
    letter-spacing: -0.5px;
  }
  .details__email {
    font-family: "Open Sans", sans-serif;
    font-size: 21px;
    line-height: 32px;
    color: var(--ink);
    margin-top: 4px;
  }
</style>
</head>
<body>
  <main class="canvas">
    <div class="card-shadow">
      <section class="card" aria-label="Clear plastic business card front">
        <div class="card__frost"></div>
        <div class="card__band"></div>
        <svg class="card__outline" viewBox="0 0 895 499" preserveAspectRatio="none" aria-hidden="true">
          <polygon points="70,1 894,1 894,429 825,498 1,498 1,70" fill="none" stroke="var(--card-edge)" stroke-width="2"/>
        </svg>
        <div class="brand-mark">
          <div class="brand-mark__square"></div>
          <p class="brand-mark__name">Light for the<br>Weary Souls</p>
        </div>
        <div class="details">
          <h1 class="details__name">Light for the<br>Weary Souls</h1>
          <div class="details__rule details__rule--top"></div>
          <p class="details__phone">555-382-7194</p>
          <div class="details__rule"></div>
          <p class="details__email">email@lightfortheweary-mail.org</p>
        </div>
      </section>
    </div>
  </main>
</body>
</html>
```